Wrenfield Home Care Retractable Banner Design

Retractable Banner Design
We need a pull up retractable banner design
85 x 206 cm.
We need the banner to use at expo's, information sessions, presentations, recruitment days. Needs to be attractive to our elderly client's and staff (care workers)
Phone number needs to be on 08 7394 2056
Website also needs to be on the banner : wrenfieldhomecare.com.au

Target Market(s)

35 +

Industry/Entity Type

aged care / community

Requirements
Must have
• Colours, fonts and logo as detailed in upload

```html
<!DOCTYPE html>
<html lang="en">
<head>
<meta charset="utf-8">
<title>Wrenfield Home Care – Pull Up Banner</title>
<link rel="stylesheet" href="https://fonts.googleapis.com/css2?family=Poppins:wght@400;600;700&display=swap">
<style>
  :root {
    --maroon: #8c1a2e;
    --maroon-deep: #7a1426;
    --rose: #b0377a;
    --ink: #3a3a3a;
    --charcoal: #333333;
    --paper: #f1f1f1;
    --paper-shade: #e4e4e4;
    --stage: #e6e8ec;
    --white: #ffffff;
  }
  * { box-sizing: border-box; margin: 0; padding: 0; }
  html, body {
    width: 1200px; height: 1200px; overflow: hidden;
    background: var(--stage);
    font-family: "Poppins", sans-serif;
  }
  .banner {
    position: absolute; left: 365px; top: 30px;
    width: 470px; height: 1140px;
    background: var(--paper);
    overflow: hidden;
    box-shadow: 0 6px 24px rgba(0,0,0,.12);
  }
  .banner-art { position: absolute; inset: 0; }
  .brand-panel {
    position: absolute; left: 0; top: 52px;
    width: 280px; height: 96px;
    background: rgba(255,255,255,.94);
    border-radius: 0 14px 14px 0;
    display: flex; align-items: center; gap: 12px;
    padding-left: 62px;
  }
  .brand-dot {
    width: 50px; height: 50px; border-radius: 50%;
    background: var(--maroon); flex: none;
  }
  .brand-name {
    color: var(--maroon); font-weight: 400;
    font-size: 20px; line-height: 1.15;
  }
  .headline {
    position: absolute; left: 42px; top: 612px;
    font-weight: 700; line-height: 1.12;
  }
  .headline-accent { display: block; color: var(--maroon); font-size: 44px; }
  .headline-main { display: block; color: var(--ink); font-size: 42px; }
  .intro {
    position: absolute; left: 42px; top: 752px; width: 340px;
    color: var(--ink); font-size: 14px; line-height: 30px;
  }
  .call-to-action {
    position: absolute; left: 40px; top: 866px;
    color: var(--maroon); font-size: 18px; font-weight: 600;
  }
  .contact {
    position: absolute; left: 42px;
    display: flex; align-items: center;
  }
  .contact-phone { top: 918px; }
  .contact-web { top: 1052px; }
  .contact-icon {
    width: 70px; height: 66px; border-radius: 6px;
    display: flex; align-items: center; justify-content: center;
    position: relative; z-index: 1;
  }
  .contact-phone .contact-icon { background: var(--maroon); outline: 1px solid var(--maroon); outline-offset: 3px; }
  .contact-web .contact-icon { background: var(--charcoal); }
  .contact-text {
    height: 54px; margin-left: -6px;
    background: var(--maroon-deep); color: var(--white);
    border-radius: 0 10px 10px 0;
    display: flex; align-items: center;
    padding-left: 28px;
  }
  .contact-phone .contact-text { width: 268px; font-size: 26px; font-weight: 700; }
  .contact-web .contact-text { width: 295px; font-size: 17px; font-weight: 600; }
</style>
</head>
<body>
<main class="banner">
  <svg class="banner-art" width="470" height="1140" viewBox="0 0 470 1140">
    <defs>
      <linearGradient id="photo-tone" x1="0" y1="0" x2="1" y2="1">
        <stop offset="0" stop-color="#c9c4bb"/>
        <stop offset=".45" stop-color="#b08c6e"/>
        <stop offset="1" stop-color="#6b5a45"/>
      </linearGradient>
      <linearGradient id="hands-tone" x1="0" y1="0" x2="1" y2="1">
        <stop offset="0" stop-color="#2a2a2a"/>
        <stop offset="1" stop-color="#c79a86"/>
      </linearGradient>
      <linearGradient id="group-tone" x1="0" y1="0" x2="1" y2="1">
        <stop offset="0" stop-color="#9aa6a0"/>
        <stop offset="1" stop-color="#b8453e"/>
      </linearGradient>
    </defs>
    <!-- soft background arc -->
    <circle class="bg-arc" cx="470" cy="820" r="330" fill="var(--paper-shade)" opacity=".5"/>
    <!-- hero photo area -->
    <path role="img" aria-label="Photo of a carer sitting arm in arm with a smiling elderly woman outdoors"
          d="M0 40 H470 V420 Q300 540 170 470 Q70 410 0 360 Z" fill="url(#photo-tone)"/>
    <!-- top right swoosh -->
    <path d="M300 0 H470 V160 Q440 40 300 0 Z" fill="var(--maroon)"/>
    <path d="M250 0 H300 Q430 30 470 160 V190 Q430 50 250 0 Z" fill="var(--white)" opacity=".85"/>
    <!-- swooshes below the photo -->
    <path d="M0 360 Q70 410 170 470 Q300 540 470 420" fill="none" stroke="var(--rose)" stroke-width="4"/>
    <path d="M0 378 Q90 440 200 520 Q330 590 470 470 V520 Q330 630 190 540 Q80 470 0 410 Z" fill="var(--white)"/>
    <path d="M0 392 Q40 440 80 480 Q40 450 0 430 Z" fill="var(--maroon)"/>
    <path d="M200 540 Q330 610 470 500 V560 Q350 650 210 560 Z" fill="var(--maroon)"/>
    <!-- round photos -->
    <circle cx="172" cy="508" r="70" fill="var(--maroon)"/>
    <circle role="img" aria-label="Photo of a young hand holding an elderly hand" cx="172" cy="508" r="64" fill="url(#hands-tone)"/>
    <circle cx="326" cy="552" r="68" fill="var(--maroon)"/>
    <circle role="img" aria-label="Photo of seniors sharing a drink together" cx="326" cy="552" r="62" fill="url(#group-tone)"/>
    <!-- bottom right swoosh -->
    <path d="M470 960 Q330 990 240 1140 H270 Q350 1010 470 985 Z" fill="var(--maroon)"/>
  </svg>

  <div class="brand-panel">
    <span class="brand-dot"></span>
    <span class="brand-name">Wrenfield<br>Home Care</span>
  </div>

  <h1 class="headline">
    <span class="headline-accent">Caring</span>
    <span class="headline-main">for Your Loved</span>
  </h1>

  <p class="intro">Lorem ipsum dolor sit amet, consectetuer, sed diam nonummy nibh euismod tincidunt ut laoreet dolore magna aliquam erat</p>

  <p class="call-to-action">Don't hesitate, Visit us now</p>

  <div class="contact contact-phone">
    <span class="contact-icon">
      <svg width="30" height="30" viewBox="0 0 24 24" aria-hidden="true">
        <path d="M6.6 10.8a15.1 15.1 0 0 0 6.6 6.6l2.2-2.2a1 1 0 0 1 1-.25 11.4 11.4 0 0 0 3.6.6 1 1 0 0 1 1 1V20a1 1 0 0 1-1 1A17 17 0 0 1 3 4a1 1 0 0 1 1-1h3.5a1 1 0 0 1 1 1c0 1.25.2 2.45.6 3.6a1 1 0 0 1-.25 1Z" fill="#fff"/>
      </svg>
    </span>
    <span class="contact-text">08 7394 2056</span>
  </div>

  <div class="contact contact-web">
    <span class="contact-icon">
      <svg width="26" height="34" viewBox="0 0 24 32" aria-hidden="true">
        <path d="M12 0C5.4 0 0 5.2 0 11.7 0 20.5 12 32 12 32s12-11.5 12-20.3C24 5.2 18.6 0 12 0Zm0 16a4.5 4.5 0 1 1 0-9 4.5 4.5 0 0 1 0 9Z" fill="#fff"/>
      </svg>
    </span>
    <span class="contact-text">wrenfieldhomecare.com.au</span>
  </div>
</main>
</body>
</html>
```